BRIGHT RIVER POWER.

I'd like my business logo.
contact name: Dennis Halvorsen
phone:0438759164
email: info@brightriverpower.net.au
website: www.brightriverpower.net.au

services:
solar
battery storage
LED lighting
energy saving solutions
general electrical
I'd like the design to look professional

Target Market(s)

Everyone

Industry/Entity Type

Business

Contact Information for Business Card

as described above

Requirements
Must have
• Id like the colours and the design to work well with my logo.

```html
<!DOCTYPE html>
<html lang="en">
<head>
<meta charset="utf-8">
<title>Bright River Power – Business Card</title>
<link href="https://fonts.googleapis.com/css2?family=Mulish:wght@400;600;700&display=swap" rel="stylesheet">
<style>
  :root {
    --backdrop: #e8e5e0;
    --card: #ffffff;
    --green: #5aae57;
    --green-soft: #8cc63f;
    --orange: #f2a627;
    --name-orange: #f08c1e;
    --shadow: rgba(60, 45, 25, 0.18);
  }
  * { margin: 0; padding: 0; box-sizing: border-box; }
  html, body {
    width: 1200px;
    height: 1022px;
    overflow: hidden;
    background: var(--backdrop);
    font-family: "Mulish", sans-serif;
  }
  .card {
    position: absolute;
    left: 220px;
    width: 760px;
    height: 465px;
    background: var(--card);
    border-radius: 22px;
    box-shadow: 0 6px 18px var(--shadow);
  }
  .card--front { top: 30px; }
  .card--back { top: 527px; display: flex; align-items: center; justify-content: center; }

  .brand {
    display: flex;
    align-items: center;
    gap: 14px;
  }
  .brand__dot {
    width: 40px;
    height: 40px;
    border-radius: 50%;
    background: var(--orange);
  }
  .brand__name {
    color: var(--green);
    font-weight: 700;
    font-size: 32px;
    letter-spacing: 0.5px;
  }
  .card--front .brand {
    position: absolute;
    left: 56px;
    top: 60px;
  }
  .card--back .brand__dot { width: 60px; height: 60px; }
  .card--back .brand__name { font-size: 48px; }

  .details {
    position: absolute;
    left: 60px;
    top: 160px;
  }
  .person {
    color: var(--name-orange);
    font-weight: 600;
    font-size: 29px;
    margin-bottom: 12px;
  }
  .contact, .services { list-style: none; }
  .contact li, .services li {
    display: flex;
    align-items: center;
    gap: 14px;
    color: var(--green);
    font-size: 19px;
    line-height: 30px;
  }
  .contact svg { width: 15px; height: 15px; flex: none; }
  .services li::before {
    content: "";
    width: 9px;
    height: 9px;
    border-radius: 50%;
    background: var(--orange);
    margin: 0 3px;
    flex: none;
  }
</style>
</head>
<body>

<section class="card card--front">
  <div class="brand">
    <span class="brand__dot"></span>
    <span class="brand__name">Bright River Power</span>
  </div>

  <div class="details">
    <p class="person">Dennis Halvorsen</p>
    <ul class="contact">
      <li>
        <svg viewBox="0 0 16 16" aria-hidden="true"><path d="M4 1.5 6.2 4 5 5.6c.8 1.9 2.4 3.5 4.3 4.3L11 8.8l2.5 2.2-1.4 2.4C7 13 3 9 2.6 3z" fill="var(--orange)"/></svg>
        0438759164
      </li>
      <li>
        <svg viewBox="0 0 16 16" aria-hidden="true"><rect x="1.5" y="3.5" width="13" height="9" rx="1" fill="none" stroke="var(--orange)" stroke-width="1.6"/><path d="M2 4l6 5 6-5" fill="none" stroke="var(--orange)" stroke-width="1.6"/></svg>
        info@brightriverpower.net.au
      </li>
      <li>
        <svg viewBox="0 0 16 16" aria-hidden="true"><circle cx="8" cy="8" r="6.3" fill="none" stroke="var(--orange)" stroke-width="1.5"/><ellipse cx="8" cy="8" rx="2.6" ry="6.3" fill="none" stroke="var(--orange)" stroke-width="1.3"/><path d="M1.8 8h12.4" stroke="var(--orange)" stroke-width="1.3"/></svg>
        www.brightriverpower.net.au
      </li>
    </ul>
    <ul class="services">
      <li>Solar</li>
      <li>Battery storage</li>
      <li>LED lighting</li>
      <li>Energy saving solutions</li>
    </ul>
  </div>
</section>

<section class="card card--back">
  <div class="brand">
    <span class="brand__dot"></span>
    <span class="brand__name">Bright River Power</span>
  </div>
</section>

</body>
</html>
```